The Vantor Codex Book Cover

"The Vantor Codex" is a book I wrote with the slogan "Unlock Performance, Spark Engagement: Master the Art of Building Winning Cultures in Today's Hybrid World". The book is designed around a methodology that's mine and that I attached. I would love to see the graphic of the methodology integrated in the design in a very subtle way. Use colors from the model but the book cover should be catchy, modern and engaging to the eye.
Overall the book is about three key elements towards success:
- (Self) Directions (purpose)
- Human experience (people and psychological safety)
- Maximize engagement
The methodology is a FLOW so flow is something that could be incorporated as well in the concept.
Low design quality
Managers and Teams

```html
<!DOCTYPE html>
<html lang="en">
<head>
<meta charset="UTF-8">
<title>The Vantor Codex — Book Cover</title>
<link rel="stylesheet" href="https://fonts.googleapis.com/css2?family=Abril+Fatface&family=Oswald:wght@500;600&family=Montserrat:wght@400;500&display=swap">
<style>
  :root {
    --backdrop: #dfe6ea;
    --cover: #eeeeee;
    --ink: #111111;
    --teal: #2f8f98;
    --teal-light: #4aa9b0;
    --muted: #333333;
    --tone-pink: #e7a6c6;
    --tone-violet: #b9a8e0;
    --tone-yellow: #e9e0a0;
    --tone-teal: #9fd3cf;
  }
  * { margin: 0; padding: 0; box-sizing: border-box; }
  html, body {
    width: 1200px;
    height: 1182px;
    overflow: hidden;
    background: var(--backdrop);
  }
  .canvas {
    width: 1200px;
    height: 1182px;
    display: flex;
    align-items: center;
    justify-content: center;
  }
  .book-cover {
    position: relative;
    width: 770px;
    height: 1100px;
    background: var(--cover);
    box-shadow: 0 10px 30px rgba(0, 0, 0, 0.12);
    text-align: center;
  }
  .tagline {
    position: absolute;
    top: 150px;
    left: 0;
    right: 0;
    font-family: "Montserrat", sans-serif;
    font-weight: 500;
    font-size: 15px;
    letter-spacing: 0.42em;
    color: var(--ink);
  }
  .title {
    position: absolute;
    top: 175px;
    left: 0;
    right: 0;
    font-family: "Abril Fatface", serif;
    font-weight: 400;
    line-height: 0.84;
  }
  .title-article {
    display: block;
    font-size: 92px;
    color: var(--ink);
  }
  .title-main {
    display: block;
    font-size: 168px;
    color: var(--ink);
  }
  .title-accent {
    display: block;
    font-size: 188px;
    background: linear-gradient(90deg, var(--teal-light), var(--teal));
    -webkit-background-clip: text;
    background-clip: text;
    color: transparent;
  }
  .subtitle {
    position: absolute;
    top: 600px;
    left: 0;
    right: 0;
    font-family: "Oswald", sans-serif;
    font-weight: 600;
    font-size: 30px;
    line-height: 1.15;
    text-transform: uppercase;
    color: var(--ink);
  }
  .methodology-art {
    position: absolute;
    top: 700px;
    left: 95px;
    width: 580px;
    height: 280px;
    border-radius: 8px;
    background: linear-gradient(100deg, var(--tone-pink), var(--tone-violet) 35%, var(--tone-yellow) 65%, var(--tone-teal));
    opacity: 0.7;
  }
  .author {
    position: absolute;
    bottom: 52px;
    left: 0;
    right: 0;
    font-family: "Montserrat", sans-serif;
    font-weight: 400;
    font-size: 36px;
    letter-spacing: 0.45em;
    padding-left: 0.45em;
    color: var(--muted);
  }
</style>
</head>
<body>
  <main class="canvas">
    <section class="book-cover">
      <p class="tagline">UNLOCK PERFORMANCE, SPARK ENGAGEMENT:</p>
      <h1 class="title">
        <span class="title-article">The</span>
        <span class="title-main">Vantor</span>
        <span class="title-accent">Codex</span>
      </h1>
      <p class="subtitle">Master the art of building winning<br>cultures in today's hybrid world</p>
      <div class="methodology-art" role="img" aria-label="Illustration of the flow methodology: a colourful segmented wheel of team members joined to a compass over a faint globe"></div>
      <p class="author">AUTHOR NAME</p>
    </section>
  </main>
</body>
</html>
```